Sophisticated, clean website reflecting my feminine, playful side to sell my abstract art,

I need a website no more than 3 pages to showcase my paintings, a little about me and some contact info. I do abstracts so looking for something a little edgy, yet feminine and current.
Updates

Hi there, These are some artists websites that I Iike: Marnelvoss.com (I like how airy it is) peterwallombry.com garethpolvens.com (I like how it scrolls) I'll need a place for a photo ( a headshot-i do not have it yet so I'll need to be able to upload that later) as well as an area for my bio. Also, it's important that I will be able to upload any new photos and descriptions easily so it should be user friendly. Lastly, I like in a sunny place so would like to have this seem upbeat and playful as that is how i like to paint. thanks-I'm trying to upload my photos now -

Target Market(s)

ppl ages 35-70 who want large scale art for their homes

Industry/Entity Type

art

Coding

Coded - Design and coding required

Number of Pages Required

3 page

Colors

Designer to choose colors to be used in the design.

Requirements
Must have
• photos of my art, a place for my bio, be easy to reach me. tasteful-nothing too "in your face" -my clients are pretty high end and organized. They like clean lines
Nice to have
• sophisticated background, muted tones in the back-similar clean font throughout-no cursive
Should not have
• too many dark areas. Too many blocks of color. Too serious.

```html
<!DOCTYPE html>
<html lang="en">
<head>
<meta charset="utf-8">
<title>Marlena Kova — Abstract Art</title>
<link href="https://fonts.googleapis.com/css2?family=Jost:wght@300;400&family=Quicksand:wght@300;400;500&display=swap" rel="stylesheet">
<style>
  :root {
    --bg: #f0f0f0;
    --ink: #4a4a4a;
    --ink-soft: #5c5c5c;
    --rule: #9a9a9a;
    --frame: #ffffff;
    --hero-a: #d9dccf;
    --hero-b: #3f9a5c;
    --hero-c: #d8c96a;
    --hero-d: #1f6f72;
    --art-a: #c4702c;
    --art-b: #2f8f8a;
    --art-c: #2a2a28;
    --art-d: #e6e1d2;
    --portrait: #dedede;
  }
  * { box-sizing: border-box; margin: 0; padding: 0; }
  html, body { width: 1200px; height: 2901px; overflow: hidden; }
  body {
    position: relative;
    background: var(--bg);
    color: var(--ink);
    font-family: "Quicksand", sans-serif;
  }

  .site-header { position: absolute; left: 0; top: 0; width: 1200px; height: 114px; border-bottom: 1px solid var(--rule); }
  .brand {
    position: absolute; left: 0; width: 1200px; top: 32px; text-align: center;
    font-family: "Jost", sans-serif; font-weight: 300; font-size: 53px; letter-spacing: 2px; color: var(--ink);
    line-height: 1;
  }
  .brand-square { display: inline-block; width: 32px; height: 40px; background: var(--ink); vertical-align: -2px; margin: 0 16px; }

  .main-nav { position: absolute; top: 130px; left: 0; width: 1200px; height: 24px; font-family: "Jost", sans-serif; font-size: 18px; color: var(--ink); }
  .main-nav a { position: absolute; color: inherit; text-decoration: none; transform: translateX(-50%); white-space: nowrap; }
  .nav-dot { position: absolute; top: 10px; width: 4px; height: 4px; background: #9a9a9a; }

  .hero {
    position: absolute; left: 0; top: 173px; width: 1200px; height: 680px;
    background:
      radial-gradient(ellipse at 78% 18%, var(--hero-c) 0%, transparent 38%),
      radial-gradient(ellipse at 30% 45%, var(--hero-b) 0%, transparent 55%),
      radial-gradient(ellipse at 75% 75%, var(--hero-d) 0%, transparent 45%),
      linear-gradient(120deg, var(--hero-a), #6fae5a 55%, #5a7a4a);
  }
  .arrow { position: absolute; }

  .section-title {
    position: absolute; font-family: "Jost", sans-serif; font-weight: 300; font-size: 54px;
    color: var(--ink); text-align: center; line-height: 1; transform: translateX(-50%); white-space: nowrap;
  }
  .title-rule { position: absolute; height: 2px; background: var(--rule); }

  .portrait-frame { position: absolute; left: 77px; top: 1033px; width: 351px; height: 412px; background: var(--frame); padding: 8px; }
  .portrait { width: 100%; height: 100%; background: linear-gradient(180deg, var(--portrait) 60%, #f4f4f4); }

  .about-copy {
    position: absolute; left: 470px; top: 1129px; width: 650px; text-align: center;
    font-size: 19px; font-weight: 400; line-height: 28px; color: var(--ink-soft);
  }
  .about-copy p { margin-bottom: 14px; }

  .gallery-frame { position: absolute; left: 122px; top: 1684px; width: 951px; height: 559px; background: var(--frame); padding: 9px; }
  .gallery-art {
    width: 100%; height: 100%;
    background:
      radial-gradient(ellipse at 15% 30%, var(--art-a) 0%, transparent 40%),
      radial-gradient(ellipse at 45% 35%, var(--art-b) 0%, transparent 40%),
      radial-gradient(ellipse at 55% 80%, var(--art-c) 0%, transparent 45%),
      radial-gradient(ellipse at 85% 40%, var(--art-d) 0%, transparent 40%),
      linear-gradient(120deg, #8a6a3a, #3d6a64 50%, #6b5a40);
  }

  .contact-lead { position: absolute; left: 0; width: 1200px; top: 2497px; text-align: center; font-size: 21px; color: var(--ink-soft); }
  .contact-list { position: absolute; left: 0; width: 1200px; top: 2567px; list-style: none; font-size: 17px; font-weight: 500; color: #333; }
  .contact-list li { height: 51px; display: flex; justify-content: center; align-items: flex-start; gap: 9px; }
  .contact-list svg { flex: none; margin-top: -2px; }
  .social-dot { width: 22px; height: 22px; border: 1.5px solid #555; border-radius: 50%; flex: none; margin-top: -1px; }

  .site-footer { position: absolute; left: 0; width: 1200px; top: 2850px; text-align: center; font-size: 14px; color: #555; }
</style>
</head>
<body>

<header class="site-header">
  <div class="brand">MARLENA<span class="brand-square"></span>KOVA</div>
  <nav class="main-nav">
    <a href="#home" style="left:303px">HOME</a>
    <span class="nav-dot" style="left:377px"></span>
    <a href="#about" style="left:491px">ABOUT ME</a>
    <span class="nav-dot" style="left:591px"></span>
    <a href="#gallery" style="left:690px">GALLERY</a>
    <span class="nav-dot" style="left:795px"></span>
    <a href="#contact" style="left:886px">CONTACT</a>
  </nav>
</header>

<section class="hero" id="home" role="img" aria-label="Close-up of an abstract painting in greens, teal and soft yellow">
  <svg class="arrow" style="left:22px;top:452px" width="28" height="46" viewBox="0 0 28 46"><polyline points="24,3 4,23 24,43" fill="none" stroke="#ffffff" stroke-width="3" opacity=".75"/></svg>
  <svg class="arrow" style="left:1136px;top:452px" width="28" height="46" viewBox="0 0 28 46"><polyline points="4,3 24,23 4,43" fill="none" stroke="#ffffff" stroke-width="3"/></svg>
</section>

<section id="about">
  <div class="portrait-frame"><div class="portrait" role="img" aria-label="Headshot of the artist"></div></div>
  <h2 class="section-title" style="left:795px;top:1033px">ABOUT ME</h2>
  <div class="title-rule" style="left:668px;top:1090px;width:254px"></div>
  <div class="about-copy">
    <p>Lorem ipsum dolor sit amet, consectetur adipiscing elit, sed do eiusmod tempor incididunt ut labore et dolore magna aliqua. Ut enim ad minim veniam, quis nostrud exercitation Lorem ipsum dolor sit amet, consect­etur adipiscing elit, sed do eiusmod tempor</p>
    <p>Duis aute irure dolor in reprehenderit in voluptate velit esse cillum dolore eu fugiat nulla pariatur. Excepteur sint occaecat cupidatat non proident, sunt in culpa qui officia deserunt mollit anim id est laborum.</p>
    <p>Sed ut perspiciatis unde pariatur. Excepteur sint occaecat cupidatat non proident, sunt in culpa qui officia deserunt mollit</p>
  </div>
</section>

<section id="gallery">
  <h2 class="section-title" style="left:599px;top:1590px">GALLERY</h2>
  <div class="title-rule" style="left:505px;top:1645px;width:181px"></div>
  <svg class="arrow" style="left:52px;top:1936px" width="30" height="50" viewBox="0 0 30 50"><polyline points="26,3 4,25 26,47" fill="none" stroke="#555" stroke-width="3"/></svg>
  <div class="gallery-frame"><div class="gallery-art" role="img" aria-label="Abstract painting in burnt orange, teal, black and white brushstrokes"></div></div>
  <svg class="arrow" style="left:1119px;top:1936px" width="30" height="50" viewBox="0 0 30 50"><polyline points="4,3 26,25 4,47" fill="none" stroke="#555" stroke-width="3"/></svg>
</section>

<section id="contact">
  <h2 class="section-title" style="left:604px;top:2398px">CONTACT ME</h2>
  <div class="title-rule" style="left:450px;top:2453px;width:318px"></div>
  <p class="contact-lead">Please get in touch with me on below details.</p>
  <ul class="contact-list">
    <li>
      <svg width="28" height="20" viewBox="0 0 28 20"><rect x="1" y="1" width="26" height="18" fill="none" stroke="#555" stroke-width="1.4"/><polyline points="1,1 14,12 27,1" fill="none" stroke="#555" stroke-width="1.4"/><line x1="1" y1="19" x2="11" y2="10" stroke="#555" stroke-width="1.2"/><line x1="27" y1="19" x2="17" y2="10" stroke="#555" stroke-width="1.2"/></svg>
      <span>info@marlenakova.com</span>
    </li>
    <li>
      <svg width="28" height="26" viewBox="0 0 28 26"><path d="M6 2 L10 7 L7.5 10 C9 14 12 17 16 19 L19 16.5 L24 20.5 L21 24 C12 23 3 14 2 5 Z" fill="none" stroke="#555" stroke-width="1.4" stroke-linejoin="round"/><path d="M15 6 A6 6 0 0 1 20 11" fill="none" stroke="#555" stroke-width="1.2"/><path d="M15 2 A10 10 0 0 1 24 11" fill="none" stroke="#555" stroke-width="1.2"/></svg>
      <span>Phone: (555) 014 2290</span>
    </li>
    <li>
      <span class="social-dot"></span>
      <span>studio @mkovaart</span>
    </li>
    <li>
      <span class="social-dot"></span>
      <span>videos @mkpainter</span>
    </li>
  </ul>
</section>

<footer class="site-footer">© 2022 Marlena Kova &nbsp; All Rights Reserved</footer>

</body>
</html>
```